Brightline Energy Product Distribution Brochure

We are looking to have our current brochure for our customers completely redesigned...the idea is to present the relevant information in an attractive way . Our website is brightlineenergyco.example where you can find more information about us. We have included a file with a rough idea of the page order and what each should include but feel free to adapt based on design. The example provided is only for context and doesnt have to be maintained. We will be using the brochure both digitally and in print form. As long as it reads easily and is eye catching, the design can be horizontal or vertical.Final deliverable should be indesign file.

"Our Brands" page: should be limited to one page (space being enough) where it has the header for each one (for example diesel generators) space for one or two lines of text and then the corresponding logos for each of the five categories
Updates

For those asking: the "our brands" page should be a single page layout where there is a header with the corresponding section and space for maybe one line of text followed by the two logos for that category. Each of the product pages should be similar in fashion to the one in the document attached: a photo of the product with some white space and space for the text to be included. We will be posting additional examples today

Target Market(s)

We want to present it to customers both digitally and in print so they can see our products

Industry/Entity Type

Power Generation

Font styles to use
Serif

Requirements
Must have
• Eye catching and able to present the information in a presentable fashion. Rest is up to you.
Nice to have
• Should incorporate the colors of our logo but can also add other depending on design

```html
<!DOCTYPE html>
<html lang="en">
<head>
<meta charset="utf-8">
<title>Brightline Energy Brochure – Index and About spread</title>
<link href="https://fonts.googleapis.com/css2?family=Michroma&family=Montserrat:wght@400;600;700;800&display=swap" rel="stylesheet">
<style>
  :root{
    --backdrop:#e4e2de;
    --paper:#ffffff;
    --paper-shade:#f1f1f1;
    --row-grey:#e6e5e5;
    --ink:#555555;
    --index-blue:#3a3f9a;
    --accent-yellow:#f2cb1f;
    --panel:rgba(28,20,12,0.86);
    --ring:#45b8dc;
    --cat-dg:#1fb3e6;
    --cat-ts:#8e44ad;
    --cat-ac:#e03131;
    --cat-ap:#f7b918;
    --cat-gc:#3db54a;
    --photo-light:#f4c418;
    --photo-mid:#b38a10;
    --photo-dark:#2e2a24;
  }
  *{box-sizing:border-box;margin:0;padding:0}
  html,body{width:1200px;height:960px;overflow:hidden}
  body{background:var(--backdrop);font-family:'Montserrat',sans-serif;position:relative}
  .spread{position:absolute;left:40px;top:180px;width:1120px;height:600px;background:var(--paper);box-shadow:0 12px 40px rgba(0,0,0,.18)}
  .spread::after{content:"";position:absolute;left:548px;top:0;width:24px;height:100%;background:linear-gradient(90deg,rgba(0,0,0,0),rgba(0,0,0,.12),rgba(0,0,0,0))}
  .page-left{position:absolute;left:0;top:0;width:560px;height:600px;background:linear-gradient(90deg,var(--paper),var(--paper-shade))}
  .photo-layer{position:absolute;left:0;top:0;width:1120px;height:600px}

  .index{position:absolute;left:56px;top:150px;width:300px}
  .index-title{font-family:'Michroma',sans-serif;font-size:26px;color:var(--index-blue);letter-spacing:1px;margin-bottom:22px}
  .index-row{display:flex;justify-content:space-between;align-items:center;height:29px;padding:0 8px;font-size:12px;color:var(--ink);text-transform:uppercase;letter-spacing:.3px}
  .index-row.shaded{background:var(--row-grey)}
  .index-row .num{font-size:11px}
  .categories{margin:4px 0 6px 72px}
  .cat{display:flex;justify-content:space-between;align-items:center;height:22px;padding:0 6px 0 10px;font-size:12px;color:#fff}
  .cat b{font-weight:800;margin-right:4px}
  .cat .num{font-size:11px}
  .cat-dg{background:var(--cat-dg)}
  .cat-ts{background:var(--cat-ts)}
  .cat-ac{background:var(--cat-ac)}
  .cat-ap{background:var(--cat-ap)}
  .cat-gc{background:var(--cat-gc)}

  .about-panel{position:absolute;left:620px;top:70px;width:460px;height:400px;background:var(--panel);padding:40px 26px 0 26px}
  .about-title{font-family:'Michroma',sans-serif;font-size:23px;color:var(--accent-yellow);letter-spacing:.5px;margin-bottom:10px}
  .about-text{font-size:8.5px;line-height:1.45;color:#eee;margin-bottom:24px;max-width:400px}
  .stats{display:grid;grid-template-columns:repeat(4,1fr);row-gap:14px;column-gap:8px}
  .stat{display:flex;flex-direction:column;align-items:center;text-align:center}
  .ring{width:84px;height:84px;border:3px solid var(--ring);border-radius:50%;display:flex;align-items:center;justify-content:center;color:#fff;font-weight:800;font-size:21px}
  .ring.small-num{font-size:16px}
  .ring svg{width:46px;height:46px}
  .stat-label{margin-top:6px;font-size:8px;font-weight:700;color:var(--accent-yellow);line-height:1.2;max-width:92px}
</style>
</head>
<body>
  <div class="spread">
    <div class="page-left"></div>

    <svg class="photo-layer" viewBox="0 0 1120 600" role="img" aria-label="Photo of a large yellow industrial diesel generator engine">
      <defs>
        <linearGradient id="engine" x1="0" y1="0" x2="1" y2="1">
          <stop offset="0" stop-color="var(--photo-dark)"/>
          <stop offset="0.35" stop-color="var(--photo-mid)"/>
          <stop offset="0.6" stop-color="var(--photo-light)"/>
          <stop offset="1" stop-color="var(--photo-mid)"/>
        </linearGradient>
      </defs>
      <path d="M230 0 L1000 0 L1120 200 L1120 600 L560 600 Q400 330 230 0 Z" fill="url(#engine)"/>
    </svg>

    <nav class="index">
      <h2 class="index-title">INDEX</h2>
      <div class="index-row"><span>About our company</span><span class="num">3</span></div>
      <div class="index-row shaded"><span>Our team</span><span class="num">4</span></div>
      <div class="index-row"><span>Our brands</span><span class="num">5</span></div>
      <div class="index-row shaded"><span>Our stock</span><span class="num">6</span></div>
      <div class="index-row"><span>Our products</span><span class="num">7</span></div>
      <div class="categories">
        <div class="cat cat-dg"><span><b>DG</b>Diesel Generators</span><span class="num">8</span></div>
        <div class="cat cat-ts"><span><b>TS</b>Transfer Switches</span><span class="num">10</span></div>
        <div class="cat cat-ac"><span><b>AC</b>Alternators</span><span class="num">12</span></div>
        <div class="cat cat-ap"><span><b>AP</b>Alternator Parts</span><span class="num">14</span></div>
        <div class="cat cat-gc"><span><b>GC</b>Generator Controls</span><span class="num">16</span></div>
      </div>
      <div class="index-row"><span>Our distributors</span><span class="num">19</span></div>
    </nav>

    <section class="about-panel">
      <h1 class="about-title">ABOUT OUR COMPANY</h1>
      <p class="about-text">We supply dependable generators, switches and parts to customers around the world, backed by decades of field know-how, a deep stock of original components and a team ready to help.</p>
      <div class="stats">
        <div class="stat"><div class="ring">40+</div><div class="stat-label">years industry experience</div></div>
        <div class="stat"><div class="ring">$4M+</div><div class="stat-label">product inventory</div></div>
        <div class="stat"><div class="ring">100%</div><div class="stat-label">original components</div></div>
        <div class="stat"><div class="ring small-num">10,000+</div><div class="stat-label">Customers served</div></div>

        <div class="stat"><div class="ring">
          <svg viewBox="0 0 46 46" aria-hidden="true"><g stroke="#fff" stroke-width="1.6" fill="#fff">
            <line x1="23" y1="23" x2="6" y2="10"/><line x1="23" y1="23" x2="40" y2="10"/><line x1="23" y1="23" x2="4" y2="28"/><line x1="23" y1="23" x2="42" y2="28"/><line x1="23" y1="23" x2="14" y2="42"/><line x1="23" y1="23" x2="32" y2="42"/>
            <circle cx="23" cy="23" r="6"/><circle cx="6" cy="10" r="2.5" fill="none"/><circle cx="40" cy="10" r="2.5" fill="none"/><circle cx="4" cy="28" r="2.5" fill="none"/><circle cx="42" cy="28" r="2.5" fill="none"/><circle cx="14" cy="42" r="2.5" fill="none"/><circle cx="32" cy="42" r="2.5" fill="none"/></g></svg>
        </div><div class="stat-label">Master Distributors</div></div>

        <div class="stat"><div class="ring">
          <svg viewBox="0 0 46 46" aria-hidden="true"><path d="M23 6 L42 22 L37 22 L37 40 L27 40 L27 30 L19 30 L19 40 L9 40 L9 22 L4 22 Z" fill="#fff"/></svg>
        </div><div class="stat-label">Single source solution</div></div>

        <div class="stat"><div class="ring">
          <svg viewBox="0 0 46 46" aria-hidden="true"><ellipse cx="16" cy="20" rx="13" ry="8" fill="#fff"/><path d="M10 26 L6 33 L16 27 Z" fill="#fff"/><ellipse cx="31" cy="22" rx="13" ry="8" fill="#fff" stroke="var(--photo-dark)" stroke-width="1.5"/><path d="M36 28 L41 35 L30 29 Z" fill="#fff"/></svg>
        </div><div class="stat-label">Fully bilingual staff</div></div>

        <div class="stat"><div class="ring">
          <svg viewBox="0 0 46 46" aria-hidden="true"><circle cx="23" cy="23" r="16" fill="#fff"/><path d="M20 14 L20 28 L32 28" stroke="var(--photo-dark)" stroke-width="3" fill="none"/><path d="M27 23 L33 28 L27 33" stroke="var(--photo-dark)" stroke-width="3" fill="none"/></svg>
        </div><div class="stat-label">Worldwide shipping</div></div>
      </div>
    </section>
  </div>
</body>
</html>
```